New B2C website design to help dads be better dads

DadHarbor is a website to help dads be the “best dad you can be.”

We require our website to be designed into a PSD format, no coding necessary.

The general concept is a two-page design. The first page is the login page, the second page is the home page. Once at the home page, rather than navigating to and from different pages, the user will push and pull through different visual and functional layers of the hierarchy. In theory, this should add to the user experience by having a visual anchor of where they are (through layered pagination) as well as improving loading times since the new information should only be a delta in data load versus a brand new page load.

The general look-and-feel we are going for is clean, simple, minimal. This means that the winning design will show us a good eye for web-optimized typography, good use of white (negative) space, and good use of a visually pleasing grid.

We require a total of 6 page "views" plus the landing page. We note that many of the views are similar to one another.
Landing page
Milestone view
Task view
Content view, articles
Content view, products
Search view
What's new view

Please review all of the additional information provided as well as the attachments for examples.

We provide the following websites as good references for:

Typography:
http://example-kelvorn.com/journal/

Use of white space:
http://www.trenvaskit.com/
http://moldrefin.com/

Example for “scrolling” page concept as well as good balance of color, typography, and white space:
http://www.qorbitalmeet.eu/

Please contact us with questions so that we can guide your design effort.
Updates

Hello designers,

The following information is added to help guide the design process:

1.  For the text dialogue below the landing page, please assume the following word count:
"why are we making dad harbor?": 250 words
"who are we?" 200 words
"what's the deal with the penguin logo?" 300 words

For the social media links, please see http://www.gravelplumbs.com/
Notice the floating "social" bar that is always to the right.  This is the concept we are going for, please try to implement this as you see fit. 

Target Market(s)

Fathers of young children ages 0-6 years old.

Industry/Entity Type

Product

Font styles to use
Sans Serif

Requirements
Must have
• Clean lines, minimal design concept

Incorporation of our logo (see attached document)

Header content is static for all views after landing page, see example

This page WILL be responsive, please keep that in mind when designing
The timeline bar should be to the left, with the timeline bar’s “milestones” also being responsive.

Designer is free to suggest font types, but any fonts used must be royalty-free and web-optimized. We request a minimum number of font types as well as fonts that load relatively fast. We reinforce that visually appealing typography is a significant factor in the winning design choice.

While we are not expecting the winning design to include code, please keep in mind that the final implementation needs to be optimized for desktop, tablet, and mobile platforms.

If you are using stock photography that is not generated by you, please provide where/how we can obtain imagery, as well as price.

All custom graphics must be available in original formats; Photoshop/GIMP layered files for layout design, and vector formats for logos, icons and other graphical elements.

Please incorporate “Blue” into design elements as you see fit, as the RGB 67 74 169 Blue is the primary color used in our brand. The complement to this blue is 255 202 0, a brownish orange. Feel free to use this color as well, although please keep it to a lesser amount.

Background color is your choice, do not feel the need to use the grey.
Should not have
• Excessive graphical content such that it affects loading times

Excessive use of too many font types such that it affects loading times

```html
<!DOCTYPE html>
<html lang="en">
<head>
<meta charset="utf-8">
<title>DadHarbor – Just Call Me Dr. Car Seat</title>
<link rel="stylesheet" href="https://fonts.googleapis.com/css2?family=Ubuntu:wght@400;500&family=Rokkitt:wght@400&display=swap">
<style>
:root{
  --brand-blue:#434aa9;
  --accent:#e0a21d;
  --accent-btn:#fcc425;
  --page-bg:#f7f7f7;
  --white:#ffffff;
  --line:#d8d8d8;
  --rule:#c9c9c9;
  --text:#6f6f6f;
  --heading:#555555;
  --muted:#9a9a9a;
  --star:#f7c21c;
  --star-off:#cfcfcf;
  --dark-icon:#555555;
}
*{box-sizing:border-box;margin:0;padding:0}
html,body{width:891px;height:1200px;overflow:hidden}
body{position:relative;background:var(--page-bg);font-family:"Ubuntu",sans-serif;color:var(--text)}
.abs{position:absolute}

/* header */
.site-header{position:absolute;left:0;top:0;width:891px;height:139px;background:var(--white);border-bottom:1px solid var(--line)}
.brand{left:74px;top:58px;display:flex;align-items:center;gap:8px;font-family:"Ubuntu",sans-serif;font-weight:500;font-size:22px;color:var(--brand-blue)}
.brand-dot{width:14px;height:14px;border-radius:50%;background:var(--brand-blue)}
.welcome{right:74px;top:14px;font-family:"Rokkitt",serif;font-size:22px;color:var(--accent);letter-spacing:.2px}
.search-input{left:522px;top:58px;width:227px;height:26px;border:1px solid var(--line);background:var(--white);font-size:10px;color:var(--muted);padding:6px 10px}
.search-btn{left:754px;top:58px;width:57px;height:26px;background:var(--accent-btn);border:1px solid #e8ad12;border-radius:2px;font-size:11px;color:#7a5a10;text-align:center;line-height:24px}
.score{left:522px;top:104px;font-size:12px;color:var(--brand-blue);display:flex;align-items:center;gap:6px}
.account-links{left:697px;top:104px;font-size:11.5px;color:var(--muted)}
.account-links span{margin:0 6px;color:#bbb}

/* timeline */
.timeline-line{left:73px;top:154px;width:1px;height:1026px;background:var(--rule)}
.milestone{left:0;display:flex;align-items:center}
.milestone .age{width:68px;text-align:right;font-size:9px;color:var(--muted);padding-right:4px}
.milestone .title{font-family:"Rokkitt",serif;font-size:18.5px;color:var(--heading);margin-left:8px}
.milestone-rule{left:74px;top:211px;width:744px;height:1px;background:var(--rule)}

/* task list */
.task-list{left:98px;top:211px;width:180px;height:271px;background:var(--white);border:1px solid var(--line);border-top:none;padding:0 7px;list-style:none}
.task-list li{height:32.6px;border-bottom:1px solid #e8e8e8;display:flex;align-items:center;font-size:11px;color:#444;padding-left:12px}
.task-list li:last-child{border-bottom:none}
.checkbox{width:8px;height:8px;border:1px solid #aaa;background:#f3f3f3;margin-right:10px;flex:none}

/* article */
.article-icon{left:292px;top:234px;width:32px;height:37px;background:var(--dark-icon);display:flex;align-items:center;justify-content:center}
.article-title{left:334px;top:230px;font-family:"Rokkitt",serif;font-size:16.5px;color:#444}
.rating{left:334px;top:258px;display:flex;align-items:center;gap:8px;font-size:10px;color:var(--muted)}
.article-card{left:292px;top:294px;width:522px;height:621px;background:var(--white);border:1px solid var(--line)}
.article-photo{left:5px;top:5px;width:512px;height:236px;background:linear-gradient(100deg,#f2a8c6 0%,#f5c7d9 35%,#c98a4a 62%,#d8a060 75%,#5a5a5a 100%)}
.article-lead{left:13px;top:258px;width:496px;font-family:"Rokkitt",serif;font-size:13px;line-height:17px;color:var(--brand-blue)}
.article-body{left:13px;top:308px;width:496px;font-size:10.2px;line-height:18.5px;color:#777}
.article-body p{margin-bottom:6px}

.rate-this{left:295px;top:933px;display:flex;align-items:center;gap:6px;font-size:10px;color:#666}

/* comments */
.comment{left:292px;top:961px;width:522px;height:73px;background:#f0f0f0;border:1px solid #e4e4e4}
.avatar{width:38px;height:38px;background:#dcdcdc;border:1px solid #cfcfcf;position:absolute;overflow:hidden}
.username{position:absolute;font-size:9.5px;color:var(--brand-blue)}
.comment-text{left:69px;top:10px;width:410px;font-size:9px;line-height:15.5px;color:#777;padding-bottom:6px;border-bottom:1px solid #d4d4d4}
.comment-time{left:69px;top:53px;font-size:9px;color:#777}
.comment-form{left:292px;top:1050px;width:522px;height:82px;background:var(--white);border:1px solid #e4e4e4;box-shadow:0 1px 2px rgba(0,0,0,.08)}
.comment-placeholder{left:70px;top:13px;font-size:9.5px;color:var(--muted)}

/* social bar */
.social-bar{left:851px;top:521px;width:40px;height:159px;background:var(--brand-blue);border-radius:3px 0 0 3px;display:flex;flex-direction:column;align-items:center;justify-content:space-around;padding:8px 0}
.social-bar span{width:18px;height:18px;border-radius:50%;background:var(--white)}
</style>
</head>
<body>

<header class="site-header">
  <div class="abs brand"><span class="brand-dot"></span>DadHarbor</div>
  <div class="abs welcome">Welcome Greg, what would you like to do today?</div>
  <div class="abs search-input">Keyword...</div>
  <div class="abs search-btn">SEARCH</div>
  <div class="abs score">
    <svg width="10" height="9" viewBox="0 0 10 9"><path d="M5 9 L0.8 4.6 A2.4 2.4 0 0 1 5 1.6 A2.4 2.4 0 0 1 9.2 4.6 Z" fill="#434aa9"/></svg>
    Super Dad Score: 10,500
  </div>
  <div class="abs account-links">My Account<span>|</span>Log out</div>
</header>

<div class="abs timeline-line"></div>
<svg class="abs" style="left:69px;top:151px" width="9" height="6" viewBox="0 0 9 6"><path d="M1 5 L4.5 1 L8 5" stroke="#bbb" fill="none" stroke-width="1.2"/></svg>
<svg class="abs" style="left:69px;top:1176px" width="9" height="6" viewBox="0 0 9 6"><path d="M1 1 L4.5 5 L8 1" stroke="#bbb" fill="none" stroke-width="1.2"/></svg>

<div class="abs milestone" style="top:166px">
  <span class="age">-3 mo</span>
  <svg width="13" height="13" viewBox="0 0 13 13"><circle cx="6.5" cy="6.5" r="6.5" fill="#555"/><path d="M8.5 6.5 H4.2 M6.3 4.3 L4.1 6.5 L6.3 8.7" stroke="#fff" stroke-width="1.5" fill="none"/></svg>
  <span class="title">Prepare for the baby arrival</span>
</div>
<div class="abs milestone-rule"></div>

<ul class="abs task-list">
  <li><span class="checkbox"></span>Buy a crib</li>
  <li><span class="checkbox"></span>Assemble the crib</li>
  <li><span class="checkbox"></span>Buy a stroller</li>
  <li><svg class="checkbox" viewBox="0 0 8 8" style="border:none;background:none;width:9px;height:9px"><rect x=".5" y=".5" width="7" height="7" fill="#f3f3f3" stroke="#aaa"/><path d="M1.8 4 L3.3 5.6 L6.3 2" stroke="#434aa9" stroke-width="1.2" fill="none"/></svg>Buy a carseat</li>
  <li><span class="checkbox"></span>Install a carseat</li>
  <li><span class="checkbox"></span>Learn to change a diaper</li>
  <li><span class="checkbox"></span>Learn to hold a baby</li>
  <li><span class="checkbox"></span>Set a fedding schedule</li>
</ul>

<div class="abs milestone" style="top:524px">
  <span class="age">0 mo</span>
  <svg width="13" height="13" viewBox="0 0 13 13"><circle cx="6.5" cy="6.5" r="6.5" fill="#555"/><path d="M4.2 6.5 H8.5 M6.4 4.3 L8.6 6.5 L6.4 8.7" stroke="#fff" stroke-width="1.5" fill="none"/></svg>
  <span class="title">What’s the Latest?</span>
</div>
<div class="abs milestone" style="top:579px">
  <span class="age">0 mo</span>
  <svg width="13" height="13" viewBox="0 0 13 13"><circle cx="6.5" cy="6.5" r="6.5" fill="#555"/><path d="M4.2 6.5 H8.5 M6.4 4.3 L8.6 6.5 L6.4 8.7" stroke="#fff" stroke-width="1.5" fill="none"/></svg>
  <span class="title">What you searched for</span>
</div>

<div class="abs article-icon">
  <svg width="16" height="19" viewBox="0 0 16 19"><path d="M4 0 H16 V19 H0 V4 Z" fill="#fff"/><path d="M0 4 H4 V0 Z" fill="#999"/></svg>
</div>
<h1 class="abs article-title">Just Call Me Dr. Car Seat</h1>
<div class="abs rating">
  <svg width="76" height="13" viewBox="0 0 76 13">
    <g fill="#f7c21c">
      <path id="st" d="M6.5 0.5 L8.2 4.4 L12.4 4.8 L9.2 7.6 L10.1 11.8 L6.5 9.6 L2.9 11.8 L3.8 7.6 L0.6 4.8 L4.8 4.4 Z"/>
      <use href="#st" x="15.5"/><use href="#st" x="31"/><use href="#st" x="46.5"/>
    </g>
    <path d="M68.5 0.5 L70.2 4.4 L74.4 4.8 L71.2 7.6 L72.1 11.8 L68.5 9.6 L64.9 11.8 L65.8 7.6 L62.6 4.8 L66.8 4.4 Z" fill="none" stroke="#f7c21c"/>
    <path d="M68.5 0.5 L68.5 9.6 L64.9 11.8 L65.8 7.6 L62.6 4.8 L66.8 4.4 Z" fill="#f7c21c"/>
  </svg>
  3,121 ratings
</div>

<article class="abs article-card">
  <div class="abs article-photo" role="img" aria-label="Photo of a smiling toddler buckled into a pink car seat beside a teddy bear wearing a seat belt"></div>
  <p class="abs article-lead">Etiam ac posuere tellus, in interdum orci. Mauris in erat erat. Vivamus in mi tempus sem condimentum ullamcorper sit amet non quam.</p>
  <div class="abs article-body">
    <p>I went out to buy my first car seat and had to earn my PhD in car seats, Newtonian physics, and anti-stain technology. Lorem ipsum dolor sit amet, consectetur adipisicing elit, sed do eiusmod tempor incididunt ut labore et dolore magna aliqua. Ut enim ad minim veniam, quis nostrud exercitation ullamco laboris nisi ut aliquip ex ea commodo consequat.</p>
    <p>&nbsp;Donec vulputate sit amet justo eget commodo. Sed tincidunt sapien tortor, eget lacinia ligula pharetra in. Nullam nunc est, eleifend vitae magna at, aliquet fringilla ipsum. In erat tortor, aliquet a egestas nec, facilisis id sapien. Suspendisse bibendum nisi non venenatis egestas. Morbi quis felis vulputate, tristique massa ac, suscipit nunc. In consequat justo eu lacus aliquet porta. Quisque mi orci, hendrerit sit amet scelerisque bibendum, euismod vel tortor. Ut cursus tellus sit amet mollis cursus. Donec eget ligula mauris. Nulla sit amet placerat magna. Vivamus interdum sapien id justo porttitor pellentesque. Suspendisse potenti. In rhoncus condimentum neque.</p>
    <p>Morbi in augue faucibus, sollicitudin ante eu, fermentum turpis. Maecenas nibh nisi, mollis iaculis malesuada id, pellentesque eu sapien. Proin quis vehicula mi. Pellentesque habitant morbi tristique senectus et netus et malesuada fames ac turpis egestas. Suspendisse aliquam rutrum quam, vel interdum massa laoreet a. Duis id odio id sapien vehicula pulvinar.</p>
  </div>
</article>

<div class="abs rate-this">Rate this :
  <svg width="78" height="13" viewBox="0 0 78 13">
    <g fill="#cfcfcf">
      <path id="so" d="M6.5 0.5 L8.2 4.4 L12.4 4.8 L9.2 7.6 L10.1 11.8 L6.5 9.6 L2.9 11.8 L3.8 7.6 L0.6 4.8 L4.8 4.4 Z"/>
      <use href="#so" x="16"/><use href="#so" x="32"/><use href="#so" x="48"/><use href="#so" x="64"/>
    </g>
  </svg>
</div>

<section class="abs comment">
  <div class="avatar" style="left:9px;top:10px"><svg width="38" height="38" viewBox="0 0 38 38"><circle cx="19" cy="14" r="7" fill="#fff"/><path d="M5 38 C5 26 33 26 33 38 Z" fill="#fff"/></svg></div>
  <span class="username" style="left:9px;top:52px">Username</span>
  <p class="abs comment-text">Suspendisse aliquam rutrum quam, vel interdum massa laoreet a. Duis id odio id sapien vehicula pulvinar. Duis condimentum, est condimentum ullamcorper fermentum.</p>
  <span class="abs comment-time">20 minutes ago</span>
</section>

<section class="abs comment-form">
  <div class="avatar" style="left:11px;top:11px"><svg width="38" height="38" viewBox="0 0 38 38"><circle cx="19" cy="14" r="7" fill="#fff"/><path d="M5 38 C5 26 33 26 33 38 Z" fill="#fff"/></svg></div>
  <span class="username" style="left:11px;top:53px">Username</span>
  <span class="abs comment-placeholder">Comment this</span>
</section>

<nav class="abs social-bar" aria-label="Share">
  <span></span><span></span><span></span><span></span>
</nav>

</body>
</html>
```